Tiskoro

We need a business card for our company is a holding for different business all are different we try to have some air of relax and fun in our projects we add pictures of the office to give you an idea od the mood of the business

Business

```html
<!DOCTYPE html>
<html lang="en">
<head>
<meta charset="utf-8">
<title>Tiskoro Business Card</title>
<link href="https://fonts.googleapis.com/css2?family=Open+Sans:wght@400;600;700;800&display=swap" rel="stylesheet">
<style>
  :root {
    --brown: #6b4429;
    --yellow: #f3e83a;
    --white: #ffffff;
    --ink: #4a3020;
    --stage: #ecebe8;
  }
  * { box-sizing: border-box; margin: 0; padding: 0; }
  html, body { width: 1200px; height: 800px; overflow: hidden; }
  body {
    background: var(--stage);
    font-family: "Open Sans", Arial, sans-serif;
    display: flex;
    align-items: center;
    justify-content: center;
    gap: 60px;
  }
  .card {
    position: relative;
    width: 520px;
    height: 297px;
    background: var(--white);
    box-shadow: 0 6px 18px rgba(0,0,0,0.12);
    overflow: hidden;
  }
  .card-shapes {
    position: absolute;
    inset: 0;
    width: 100%;
    height: 100%;
  }
  .brand {
    position: absolute;
    display: flex;
    align-items: center;
    gap: 10px;
  }
  .brand-dot {
    width: 26px;
    height: 26px;
    border-radius: 50%;
    background: var(--yellow);
  }
  .brand-name {
    font-weight: 800;
    font-size: 34px;
    color: var(--brown);
    letter-spacing: -0.5px;
  }
  .card-front .brand { left: 150px; top: 118px; }
  .card-back .brand { left: 178px; top: 106px; }
  .card-back .brand-name { font-size: 40px; }
  .card-back .brand-dot { width: 30px; height: 30px; }

  .contact-list {
    position: absolute;
    left: 26px;
    top: 52px;
    list-style: none;
    font-size: 9.5px;
    color: var(--ink);
    line-height: 15px;
  }
  .contact-list li { display: flex; align-items: center; gap: 7px; }
  .contact-icon { width: 9px; height: 9px; flex: none; fill: var(--ink); }

  .holder {
    position: absolute;
    left: 218px;
    bottom: 22px;
    color: var(--ink);
  }
  .holder-name {
    font-weight: 700;
    font-size: 13px;
    letter-spacing: 1px;
    text-transform: uppercase;
  }
  .holder-role { font-size: 10px; }
</style>
</head>
<body>

  <section class="card card-front">
    <svg class="card-shapes" viewBox="0 0 560 320" preserveAspectRatio="none" aria-hidden="true">
      <rect width="560" height="320" fill="var(--brown)"/>
      <path d="M0,38 C190,22 330,60 365,175 C385,245 405,295 415,320 L0,320 Z" fill="var(--white)"/>
      <path d="M0,40 C150,30 290,55 345,135 C300,80 180,52 0,58 Z" fill="var(--yellow)"/>
      <path d="M440,320 C425,255 440,200 480,170 C465,235 475,285 505,320 Z" fill="var(--white)"/>
    </svg>

    <ul class="contact-list">
      <li><svg class="contact-icon" viewBox="0 0 10 10"><rect x="1.5" y="0.5" width="7" height="9" rx="1" fill="none" stroke="currentColor" style="stroke:var(--ink)"/></svg>014 728 3051</li>
      <li><svg class="contact-icon" viewBox="0 0 10 10"><path d="M2 0.5 L4 2.5 L3 4 C4 5.8 4.5 6.3 6 7 L7.5 6 L9.5 8 L8 9.5 C4 9 1 6 0.5 2 Z"/></svg>014 728 3051</li>
      <li><svg class="contact-icon" viewBox="0 0 10 10"><path d="M0.5 2 H9.5 V8 H0.5 Z M0.5 2 L5 5.5 L9.5 2" fill="none" stroke="currentColor" style="stroke:var(--ink)"/></svg>hello@tiskoro.com</li>
      <li><svg class="contact-icon" viewBox="0 0 10 10"><circle cx="5" cy="5" r="4.3" fill="none" stroke="currentColor" style="stroke:var(--ink)"/><path d="M0.7 5 H9.3 M5 0.7 C2.5 3 2.5 7 5 9.3 M5 0.7 C7.5 3 7.5 7 5 9.3" fill="none" style="stroke:var(--ink)" stroke-width="0.7"/></svg>www.tiskoro.com</li>
      <li><svg class="contact-icon" viewBox="0 0 10 10"><path d="M5 0.5 C7.3 0.5 8.5 2.2 8.5 3.8 C8.5 6 5 9.5 5 9.5 C5 9.5 1.5 6 1.5 3.8 C1.5 2.2 2.7 0.5 5 0.5 Z M5 2.5 A1.3 1.3 0 1 0 5.01 2.5 Z"/></svg>27 Harbour Lane, 4th Floor, Riverton</li>
    </ul>

    <div class="brand">
      <span class="brand-dot"></span>
      <span class="brand-name">Tiskoro</span>
    </div>

    <div class="holder">
      <p class="holder-name">Marek Olsen</p>
      <p class="holder-role">Managing Director</p>
    </div>
  </section>

  <section class="card card-back">
    <div class="brand">
      <span class="brand-dot"></span>
      <span class="brand-name">Tiskoro</span>
    </div>
  </section>

</body>
</html>
```